Vornel Wellness Business Card

A Double Sided Business Card

I am a private company in Melbourne, Australia, working in the Health industry. I am a nutritionist and lifestyle coach, whom specialises in using raw foods ie. fruits/nuts/vegetables to help heal my clients and enable them to achieve their ultimate state of health.

I want a sophisticated design and colour for my card that appeals to both men and women from teenage through to elderly.

Front of Card:

Red apple peel spiral in the shape of an apple. I would like a leaf/leaves coming off the stem of the apple. Please see attachments for example.

***On Right Hand side of Image is business Name: Vornel Wellness

Underneath LOGO use slogan " Let Food Be Your Medicine"

***Use Deep Red and Blues for Text Colouring

Back of Card:

Marisol Dekkert
Nutritional Specialist and Lifestyle Coach

Specialising in: Diseased Conditions
Weight Management
Achieving your Ultimate State of Health

enquiries@vornelwellness.com.au 0457 396 504

**Make sure the front design of the card flows onto the back.
Updates

Email address has been amended, Also more specific details have been given for apple peel Image, and another image attached as example of Leaf on stem of apple.

I little more insight into what sort of feel were trying to create. We're apart of the health industry, and we want the card to have a medical/clinical feeling about it.

Target Market(s)

Males and Females from teenages to elderly

Industry/Entity Type

Business

Requirements
Must have
• Red Apple Peel Spiral, in the shape of an apple, with a leaf/leaves attached to stem.
***Must be in the shape of an apple
***Please use coloring on inside of apple peel to resemble inside of an apple.
Nice to have
• I would like my card to have a clinical feel.
Should not have
• We don't want the image of the apple to look like a Christmas decoration

```html
<!DOCTYPE html>
<html lang="en">
<head>
<meta charset="utf-8">
<title>Vornel Wellness Business Card</title>
<link rel="stylesheet" href="https://fonts.googleapis.com/css2?family=Questrial&display=swap">
<style>
  :root {
    --bg: #ece9e4;
    --card: #ffffff;
    --sky: #00aedf;
    --sky-deep: #0096c7;
    --grey-1: #e6e6e8;
    --grey-2: #cfd0d3;
    --red: #d8262c;
    --navy: #262a6e;
    --blue: #3b4ea3;
    --ink: #1d1d22;
  }
  * { box-sizing: border-box; margin: 0; padding: 0; }
  html, body { width: 1200px; height: 900px; overflow: hidden; }
  body {
    background: var(--bg);
    font-family: "Questrial", sans-serif;
    position: relative;
  }
  .card {
    position: absolute;
    background: var(--card);
    box-shadow: 0 6px 18px rgba(0,0,0,.18);
    overflow: hidden;
  }
  .card__art { position: absolute; inset: 0; width: 100%; height: 100%; }

  /* Back card */
  .card--back { left: 45px; top: 45px; width: 625px; height: 395px; }
  .profile {
    position: absolute; left: 0; width: 100%;
    top: 140px; text-align: center; padding-left: 100px;
  }
  .profile__name { color: var(--red); font-size: 27px; font-weight: 400; }
  .profile__role { color: var(--navy); font-size: 18px; line-height: 1.15; }
  .specialties {
    position: absolute; left: 0; width: 100%; top: 232px;
    text-align: center; padding-left: 100px;
  }
  .specialties__title { color: var(--navy); font-size: 19px; }
  .specialties__list { list-style: none; color: var(--ink); font-size: 16px; line-height: 1.35; }
  .specialties__list li { display: inline; }
  .specialties__list li::before { content: "·"; }
  .specialties__list li + li { margin-left: 10px; }
  .specialties__list li.wide { display: block; margin-left: 0; }
  .contact { position: absolute; left: 48px; top: 322px; list-style: none; }
  .contact li { display: flex; align-items: center; gap: 8px; color: #ffffff; font-size: 17px; line-height: 30px; }
  .contact svg { width: 22px; height: 22px; }
  .mark-dot { position: absolute; right: 28px; top: 290px; width: 62px; height: 62px; border-radius: 50%; background: var(--red); }

  /* Front card */
  .card--front { left: 565px; top: 425px; width: 600px; height: 385px; }
  .brand { position: absolute; left: 100px; top: 98px; display: flex; align-items: center; gap: 18px; }
  .brand__dot { width: 122px; height: 122px; border-radius: 50%; background: var(--red); flex: none; }
  .brand__name { color: var(--red); font-size: 44px; line-height: 1; white-space: nowrap; }
  .brand__tagline { color: var(--blue); font-size: 21px; margin-top: 6px; white-space: nowrap; }
</style>
</head>
<body>

<section class="card card--back" aria-label="Business card, back">
  <svg class="card__art" viewBox="0 0 625 395" preserveAspectRatio="none" aria-hidden="true">
    <path d="M0 0 H625 V395 H0 Z" fill="#f4f4f5"/>
    <path d="M0 40 C180 10 420 20 625 70 V150 C420 90 200 110 0 140 Z" fill="var(--grey-1)"/>
    <path d="M0 125 C200 120 420 80 625 55 V150 C430 180 220 240 0 235 Z" fill="var(--sky)"/>
    <path d="M625 150 C430 180 220 240 0 235 V255 C240 260 460 220 625 195 Z" fill="#ffffff"/>
    <path d="M410 230 C520 220 560 260 470 300 C380 330 200 320 40 300 C220 310 420 280 470 260 C520 240 480 228 410 230 Z" fill="var(--grey-2)"/>
    <path d="M0 305 C200 300 460 320 625 265 V395 H0 Z" fill="var(--sky)"/>
    <path d="M0 385 C200 400 420 370 625 330 V395 H0 Z" fill="#f4f4f5"/>
  </svg>

  <div class="profile">
    <h1 class="profile__name">Marisol Dekkert</h1>
    <p class="profile__role">Nutritional Specialist<br>Lifestyle Coach</p>
  </div>

  <div class="specialties">
    <h2 class="specialties__title">Specialising in:</h2>
    <ul class="specialties__list">
      <li>Diseased Conditions</li><li>Weight Management</li>
      <li class="wide">Achieving your Ultimate State of Health</li>
    </ul>
  </div>

  <ul class="contact">
    <li>
      <svg viewBox="0 0 22 22" aria-hidden="true"><circle cx="11" cy="11" r="11" fill="var(--red)"/><circle cx="11" cy="11" r="6" fill="none" stroke="#fff" stroke-width="1.4"/><path d="M5 11 H17 M11 5 C8 8 8 14 11 17 M11 5 C14 8 14 14 11 17" fill="none" stroke="#fff" stroke-width="1.2"/></svg>
      info@vornelwellness.com.au
    </li>
    <li>
      <svg viewBox="0 0 22 22" aria-hidden="true"><circle cx="11" cy="11" r="11" fill="var(--red)"/><path d="M7 6 L9.5 5.5 L10.5 8.5 L9 9.5 C9.6 11 10.8 12.3 12.4 13 L13.5 11.5 L16.4 12.6 L16 15.2 C11 15.5 6.5 11 7 6 Z" fill="#fff"/></svg>
      0457 396 504
    </li>
  </ul>

  <span class="mark-dot" aria-hidden="true"></span>
</section>

<section class="card card--front" aria-label="Business card, front">
  <svg class="card__art" viewBox="0 0 600 385" preserveAspectRatio="none" aria-hidden="true">
    <path d="M0 0 H600 V385 H0 Z" fill="#f6f6f7"/>
    <path d="M0 20 C180 0 400 40 600 30 V120 C420 80 200 90 0 110 Z" fill="var(--grey-1)"/>
    <path d="M0 110 C200 95 420 100 600 150 V200 C420 160 220 150 0 160 Z" fill="#ffffff"/>
    <path d="M0 215 C200 205 400 230 600 195 V300 C420 330 220 310 0 300 Z" fill="var(--sky)"/>
    <path d="M0 200 C220 190 420 215 600 180 V195 C400 230 200 205 0 215 Z" fill="var(--grey-2)"/>
    <path d="M0 300 C220 310 420 330 600 300 V385 H0 Z" fill="var(--grey-1)"/>
    <path d="M0 335 C240 370 430 360 600 345 V385 H0 Z" fill="#ffffff"/>
  </svg>

  <div class="brand">
    <span class="brand__dot" aria-hidden="true"></span>
    <div>
      <p class="brand__name">Vornel Wellness</p>
      <p class="brand__tagline">Let Food Be Your Medicine</p>
    </div>
  </div>
</section>

</body>
</html>
```